Dorvik Electric Ltd

Looking for a single page website and Facebook page design. I am an electrical contractor based on Vancouver Island. I do service, custom homes, residential and commercial installations. My company just started out, so I don't have any pictures of installs yet. I have 25 years experience. I would like the colors to be my logo colors black and I have a black Brandt Halvard that will be my vehicle which I will have a wrap for.
Updates

I just posted the contest today, not sure why the deadline is the same day.

Industry/Entity Type

Electrician

Requirements
Must have
• Services provided, About me section, quote section,
Nice to have
• I am not quite sure yet, I need to see some designs first .

```html
<!DOCTYPE html>
<html lang="en">
<head>
<meta charset="utf-8">
<title>Dorvik Electric Ltd</title>
<link href="https://fonts.googleapis.com/css2?family=Krona+One&family=Roboto:wght@400;500;700&display=swap" rel="stylesheet">
<style>
:root{
  --yellow:#f5b301;
  --black:#000;
  --panel:#0b0b0b;
  --card:#121212;
  --white:#fff;
  --muted:#d8d8d8;
}
*{box-sizing:border-box;margin:0;padding:0}
html,body{width:1200px;height:4195px;overflow:hidden;background:var(--black)}
body{position:relative;font-family:'Roboto',sans-serif;color:var(--white)}
.abs{position:absolute}
.display{font-family:'Krona One',sans-serif;text-transform:uppercase;letter-spacing:1px}
.eyebrow{color:var(--yellow);font-weight:500;font-size:16px;text-transform:uppercase}
.btn{position:absolute;background:var(--yellow);color:var(--white);font-weight:700;text-transform:uppercase;display:flex;align-items:center;justify-content:center;border-radius:3px}
.center{left:0;width:1200px;text-align:center}
.photo{position:absolute}

/* header */
.logo-tab{left:78px;top:0;width:200px;height:78px;background:var(--black);border-radius:0 0 10px 10px}
.brand{display:flex;align-items:center;gap:10px;font-weight:700;color:var(--white)}
.brand .dot{width:26px;height:26px;border:3px solid var(--yellow);border-radius:50%}
.nav{left:353px;top:34px;display:flex;gap:29px;font-size:14px;font-weight:500}
.nav .active{color:var(--yellow)}
.callbox{left:892px;top:0;width:308px;height:78px;background:var(--yellow);display:flex;align-items:center;padding-left:16px;gap:16px}
.phone-ring{width:44px;height:44px;border-radius:50%;background:var(--black);display:flex;align-items:center;justify-content:center}
.call-label{font-size:12px;font-weight:500}
.call-num{font-size:21px;font-weight:700}

/* hero */
.hero-bar{left:111px;top:264px;width:4px;height:237px;background:var(--white)}
.hero-dots{left:1012px;top:688px;display:flex;gap:14px;align-items:center}
.hero-dots span{width:5px;height:5px;border-radius:50%;background:var(--white)}
.hero-dots .on{width:18px;height:18px;border:2px solid var(--white);background:none;display:flex;align-items:center;justify-content:center}

/* about */
.about-text{left:635px;top:1016px;width:454px;font-size:14px;line-height:27px;color:var(--muted);text-align:justify}
.about-text p+p{margin-top:18px}

/* services */
.card{position:absolute;top:1604px;width:308px;height:431px;background:var(--black)}
.card .img{position:absolute;left:6px;top:6px;width:296px;height:209px}
.card h3{position:absolute;top:240px;width:100%;text-align:center;font-size:16px;font-weight:500}
.card .rule{position:absolute;top:268px;left:129px;width:50px;height:2px;background:var(--yellow)}
.card p{position:absolute;top:286px;left:14px;width:280px;text-align:center;font-size:13px;line-height:23px;color:var(--muted)}
.card .btn{left:97px;top:371px;width:115px;height:39px;font-size:11px}

/* why */
.feat{position:absolute;font-size:17px;font-weight:500;line-height:26px}
.feat.l{text-align:right}
.ficon{position:absolute;width:82px;height:82px;border-radius:50%;background:var(--yellow);display:flex;align-items:center;justify-content:center}

/* testimonials */
.tcard{position:absolute;top:2789px;width:314px;height:226px;background:var(--card);padding:30px 20px}
.tcard p{font-size:14px;line-height:25px;color:var(--muted)}
.tcard .who{position:absolute;left:20px;top:156px;display:flex;align-items:center;gap:10px}
.avatar{width:48px;height:48px;border-radius:50%}
.tcard .name{font-size:15px;font-weight:500}
.stars{color:var(--yellow);font-size:12px;letter-spacing:1px}
.quote{position:absolute;right:20px;top:164px;font-family:Georgia,serif;font-size:70px;line-height:60px;color:#3a3a3a}

/* blog */
.post{position:absolute;top:3321px;width:309px}
.post .img{width:309px;height:223px}
.post .date{margin-top:22px;font-size:10px;display:flex;gap:8px;align-items:center}
.post .date i{width:10px;height:9px;background:var(--yellow)}
.post h4{margin-top:13px;font-size:15px;font-weight:700}
.post p{margin-top:8px;font-size:13px;line-height:23px;color:var(--muted)}
.post .more{margin-top:10px;color:var(--yellow);font-size:13px;font-weight:700;display:flex;align-items:center;gap:8px}
.arrow{width:13px;height:13px;border-radius:50%;background:var(--yellow);display:inline-flex;align-items:center;justify-content:center}

/* footer */
.fcol h5{font-size:17px;font-weight:500;margin-bottom:22px}
.fcol li{list-style:none;font-size:14px;height:36px;display:flex;gap:16px;color:var(--muted)}
.fcol li .arrow{margin-top:2px}
.fcol li .ic{width:13px;flex:none;color:var(--yellow);text-align:center}
.social{display:flex;gap:8px}
.social span{width:28px;height:28px;border-radius:50%}
</style>
</head>
<body>

<!-- HERO -->
<svg class="abs" style="left:0;top:0" width="1200" height="830" aria-hidden="true">
  <defs>
    <linearGradient id="heroSky" x1="0" y1="0" x2="0" y2="1">
      <stop offset="0" stop-color="#1d2a45"/>
      <stop offset=".55" stop-color="#5a5660"/>
      <stop offset="1" stop-color="#3a2c22"/>
    </linearGradient>
  </defs>
  <polygon points="0,0 1200,0 1200,765 0,659" fill="url(#heroSky)" role="img" aria-label="Photo of a modern lit house at dusk"/>
  <polygon points="0,659 900,740 0,830" fill="var(--yellow)"/>
</svg>

<div class="abs logo-tab"></div>
<div class="abs brand" style="left:110px;top:26px;font-size:12px"><span class="dot"></span>DORVIK ELECTRIC Ltd</div>
<nav class="abs nav"><span class="active">HOME</span><span>ABOUT US</span><span>SERVICES</span><span>TESTIMONIALS</span><span>CONTACT US</span></nav>
<div class="abs callbox">
  <div class="phone-ring"><svg width="20" height="20" viewBox="0 0 24 24"><path d="M6.6 10.8a15 15 0 006.6 6.6l2.2-2.2c.3-.3.7-.4 1-.2 1.1.4 2.3.6 3.6.6.6 0 1 .4 1 1V20c0 .6-.4 1-1 1A17 17 0 013 4c0-.6.4-1 1-1h3.5c.6 0 1 .4 1 1 0 1.3.2 2.5.6 3.6.1.3 0 .7-.2 1z" fill="#fff"/></svg></div>
  <div><div class="call-label">CALL US:</div><div class="call-num">044-555 018 274</div></div>
</div>

<div class="abs hero-bar"></div>
<div class="abs" style="left:147px;top:276px;font-size:23px;font-weight:500">WELCOME TO</div>
<div class="abs display" style="left:147px;top:310px;font-size:31px">Dorvik Electric Ltd</div>
<div class="abs" style="left:147px;top:362px;width:500px;font-size:16px;line-height:26px">Lorem ipsum dolor sit amet, consectetur adipiscing elit, sed do eiusmod tempor incididunt ut magna aliqua.</div>
<div class="btn" style="left:148px;top:436px;width:161px;height:49px;font-size:15px">GET STARTED</div>
<div class="abs hero-dots"><span></span><span class="on"><span></span></span><span></span><span></span></div>

<!-- ABOUT -->
<div class="photo" style="left:111px;top:905px;width:454px;height:417px;background:linear-gradient(135deg,#8b8e92,#c8c9c4 55%,#6f7a42)" role="img" aria-label="Photo of an electrician in a hard hat wiring a panel"></div>
<div class="abs eyebrow" style="left:635px;top:922px">About Us</div>
<div class="abs display" style="left:633px;top:952px;font-size:28px">Dorvik Electric</div>
<div class="abs about-text">
  <p>Lorem ipsum dolor sit amet, consectetur adipiscing elit, sed do eiusmod tempor incididunt ut labore et dolore magna aliqua. Ut enim ad minim veniam, quis nostrud exercitation ullamco laboris nisi ut aliquip ex ea commodo consequat.</p>
  <p>Duis aute irure dolor in reprehenderit in voluptate velit esse cillum dolore eu fugiat nulla pariatur. Excepteur sint occaecat cupidatat non proident, sunt in culpa qui officia id est laborum.</p>
</div>
<div class="btn" style="left:635px;top:1258px;width:131px;height:46px;font-size:14px">READ MORE</div>
<div class="abs" style="left:802px;top:1262px;display:flex;gap:16px;align-items:center">
  <div style="width:38px;height:38px;border-radius:50%;background:#fff;display:flex;align-items:center;justify-content:center"><svg width="18" height="18" viewBox="0 0 24 24"><path d="M6.6 10.8a15 15 0 006.6 6.6l2.2-2.2c.3-.3.7-.4 1-.2 1.1.4 2.3.6 3.6.6.6 0 1 .4 1 1V20c0 .6-.4 1-1 1A17 17 0 013 4c0-.6.4-1 1-1h3.5c.6 0 1 .4 1 1 0 1.3.2 2.5.6 3.6.1.3 0 .7-.2 1z" fill="#000"/></svg></div>
  <div><div class="call-label">CALL US:</div><div class="call-num" style="color:var(--yellow)">044-555 018 274</div></div>
</div>

<!-- SERVICES -->
<section class="abs" style="left:0;top:1416px;width:1200px;height:697px;background:var(--panel)"></section>
<div class="abs eyebrow center" style="top:1494px">What We Do</div>
<div class="abs display center" style="top:1524px;font-size:28px">Our Services</div>
<div class="card" style="left:111px"><div class="img" style="background:linear-gradient(135deg,#e8e6e2,#9a8c7a 60%,#2e3a4a)" role="img" aria-label="Photo of a custom home kitchen"></div><h3>CUSTOM HOMES</h3><div class="rule"></div><p>At vero eos et accusamus et iusto odio dignis simos ducimus qui blanditiis praesentium voluptatum deleniti atquea.</p><div class="btn">READ MORE</div></div>
<div class="card" style="left:446px"><div class="img" style="background:linear-gradient(135deg,#d9d9d6,#5a6f9c 55%,#c9b9a5)" role="img" aria-label="Photo of an electrician installing a kitchen outlet"></div><h3>RESIDENTIAL INSTALLATIONS</h3><div class="rule"></div><p>At vero eos et accusamus et iusto odio dignis simos ducimus qui blanditiis praesentium voluptatum deleniti atquea.</p><div class="btn">READ MORE</div></div>
<div class="card" style="left:780px"><div class="img" style="background:linear-gradient(135deg,#7a6a55,#c7a33a 55%,#e6d27a)" role="img" aria-label="Photo of two electricians testing a commercial panel"></div><h3>COMMERCIAL INSTALLATIONS</h3><div class="rule"></div><p>At vero eos et accusamus et iusto odio dignis simos ducimus qui blanditiis praesentium voluptatum deleniti atquea.</p><div class="btn">READ MORE</div></div>

<!-- WHY CHOOSE -->
<div class="abs eyebrow center" style="top:2186px">Why Choose</div>
<div class="abs display center" style="top:2215px;font-size:28px">Dorvik Electric?</div>
<div class="photo" style="left:464px;top:2295px;width:252px;height:394px;background:linear-gradient(180deg,#7a7a7a,#2f4fa8 35%,#27408a)" role="img" aria-label="Photo of a smiling electrician in blue overalls holding a cable coil"></div>

<div class="feat l" style="right:829px;top:2339px">Servicing inland Empire<br>24-7-365</div>
<div class="ficon" style="left:386px;top:2324px"><svg width="40" height="40" viewBox="0 0 24 24" fill="none" stroke="#fff" stroke-width="1.6"><rect x="3" y="5" width="18" height="16" rx="2"/><path d="M3 10h18M8 3v4M16 3v4"/></svg></div>
<div class="feat l" style="right:873px;top:2444px">Cost Effective Options<br>Available</div>
<div class="ficon" style="left:343px;top:2429px"><svg width="40" height="40" viewBox="0 0 24 24" fill="none" stroke="#fff" stroke-width="1.6"><circle cx="12" cy="9" r="6"/><path d="M12 6v6M3 20h18"/></svg></div>
<div class="feat l" style="right:863px;top:2553px">Residential &amp;<br>Commercial</div>
<div class="ficon" style="left:350px;top:2538px"><svg width="40" height="40" viewBox="0 0 24 24" fill="none" stroke="#fff" stroke-width="1.6"><path d="M3 21V10l6-5 6 5v11zM15 21V13h6v8"/></svg></div>

<div class="ficon" style="left:683px;top:2324px"><svg width="40" height="40" viewBox="0 0 24 24" fill="none" stroke="#fff" stroke-width="1.6"><path d="M12 3l2 4 4 .5-3 3 .8 4-3.8-2-3.8 2 .8-4-3-3 4-.5z"/></svg></div>
<div class="feat" style="left:780px;top:2339px">100% Satisfaction<br>Guarantee</div>
<div class="ficon" style="left:729px;top:2429px"><svg width="40" height="40" viewBox="0 0 24 24" fill="none" stroke="#fff" stroke-width="1.6"><path d="M4 21V8h6v13M10 12h10v9M2 21h20M7 3v5"/></svg></div>
<div class="feat" style="left:825px;top:2444px">Focus on remodels and new<br>construction</div>
<div class="ficon" style="left:722px;top:2538px"><svg width="40" height="40" viewBox="0 0 24 24" fill="none" stroke="#fff" stroke-width="1.6"><circle cx="12" cy="12" r="9"/><path d="M12 7v5l3 2"/></svg></div>
<div class="feat" style="left:817px;top:2553px">Call or Chat with us<br>Anytime</div>

<!-- TESTIMONIALS -->
<svg class="abs" style="left:0;top:2689px" width="1200" height="448" aria-hidden="true">
  <rect width="1200" height="448" fill="#050505"/>
  <polygon points="0,0 404,0 171,448 0,448" fill="var(--yellow)"/>
</svg>
<div class="abs eyebrow" style="left:85px;top:2779px;color:#fff">Testimonials</div>
<div class="abs display" style="left:85px;top:2816px;font-size:25px;line-height:35px">What Our<br>Customer Says</div>
<div class="photo" style="left:0;top:2971px;width:492px;height:163px;background:linear-gradient(180deg,#2a2a2a,#111);border-radius:40px 60px 10px 10px" role="img" aria-label="Photo of the black Brandt Halvard work truck with company wrap"></div>
<div class="tcard" style="left:461px"><p>Lorem ipsum dolor sit amet, consectetur adipiscing elit, sed do eiusmod tempor incididunt ut labore et dolore magna minim veniam, quis aliqua.</p><div class="who"><div class="avatar" style="background:#8a8f96" role="img" aria-label="Customer portrait"></div><div><div class="name">Tom Hadley</div><div class="stars">★★★★★</div></div></div><div class="quote">&#8220;</div></div>
<div class="tcard" style="left:803px"><p>Lorem ipsum dolor sit amet, consectetur adipiscing elit, sed do eiusmod tempor incididunt ut labore et dolore magna minim veniam, quis aliqua.</p><div class="who"><div class="avatar" style="background:#c9a98f" role="img" aria-label="Customer portrait"></div><div><div class="name">Tom Hadley</div><div class="stars">★★★★★</div></div></div><div class="quote">&#8220;</div></div>

<!-- BLOG -->
<div class="abs eyebrow center" style="top:3211px">News</div>
<div class="abs display center" style="top:3241px;font-size:28px">Latest Blog</div>
<article class="post" style="left:111px"><div class="img" style="background:linear-gradient(135deg,#2b4a6e,#c98a45 55%,#e2b36a)" role="img" aria-label="Photo of an electrician with tools and cable"></div><div class="date"><i></i>01 Jan 2022</div><h4>SED UT PERSPICIATIS UNDE OMNIS</h4><p>At vero eos et accusamus et iusto odio dignis simos ducimus qui blanditiis praesentium volu ptatum deleniti atquea.</p><div class="more">READ MORE <span class="arrow"><svg width="7" height="7" viewBox="0 0 8 8"><path d="M2 1l3 3-3 3" stroke="#000" stroke-width="1.6" fill="none"/></svg></span></div></article>
<article class="post" style="left:446px"><div class="img" style="background:linear-gradient(135deg,#e9e4da,#b89a6a 55%,#2b3550)" role="img" aria-label="Photo of a bright kitchen with pendant lights"></div><div class="date"><i></i>01 Jan 2022</div><h4>SED UT PERSPICIATIS UNDE OMNIS</h4><p>At vero eos et accusamus et iusto odio dignis simos ducimus qui blanditiis praesentium volu ptatum deleniti atquea.</p><div class="more">READ MORE <span class="arrow"><svg width="7" height="7" viewBox="0 0 8 8"><path d="M2 1l3 3-3 3" stroke="#000" stroke-width="1.6" fill="none"/></svg></span></div></article>
<article class="post" style="left:780px"><div class="img" style="background:linear-gradient(135deg,#f0efec,#c9ccd0 55%,#5a7a9a)" role="img" aria-label="Photo of an electrician installing a ceiling light"></div><div class="date"><i></i>01 Jan 2022</div><h4>SED UT PERSPICIATIS UNDE OMNIS</h4><p>At vero eos et accusamus et iusto odio dignis simos ducimus qui blanditiis praesentium volu ptatum deleniti atquea.</p><div class="more">READ MORE <span class="arrow"><svg width="7" height="7" viewBox="0 0 8 8"><path d="M2 1l3 3-3 3" stroke="#000" stroke-width="1.6" fill="none"/></svg></span></div></article>

<!-- FOOTER -->
<svg class="abs" style="left:0;top:3712px" width="1200" height="483" aria-hidden="true">
  <polygon points="0,70 1200,0 1200,483 0,483" fill="#0e0e0e"/>
  <polygon points="650,122 1200,0 1200,171" fill="var(--yellow)"/>
</svg>
<div class="abs" style="left:111px;top:3915px;width:215px;text-align:center">
  <div style="width:110px;height:110px;margin:0 auto 14px;border:4px solid #fff;border-radius:50%"></div>
  <div style="font-size:19px;font-weight:500">DORVIK ELECTRIC Ltd</div>
</div>
<div class="abs fcol" style="left:412px;top:3909px"><h5>NAVIGATION</h5><ul>
  <li><span class="arrow"><svg width="7" height="7" viewBox="0 0 8 8"><path d="M2 1l3 3-3 3" stroke="#000" stroke-width="1.6" fill="none"/></svg></span>Home</li>
  <li><span class="arrow"><svg width="7" height="7" viewBox="0 0 8 8"><path d="M2 1l3 3-3 3" stroke="#000" stroke-width="1.6" fill="none"/></svg></span>About Us</li>
  <li><span class="arrow"><svg width="7" height="7" viewBox="0 0 8 8"><path d="M2 1l3 3-3 3" stroke="#000" stroke-width="1.6" fill="none"/></svg></span>Services</li>
  <li><span class="arrow"><svg width="7" height="7" viewBox="0 0 8 8"><path d="M2 1l3 3-3 3" stroke="#000" stroke-width="1.6" fill="none"/></svg></span>Testimonials</li>
  <li><span class="arrow"><svg width="7" height="7" viewBox="0 0 8 8"><path d="M2 1l3 3-3 3" stroke="#000" stroke-width="1.6" fill="none"/></svg></span>Contact Us</li>
</ul></div>
<div class="abs fcol" style="left:633px;top:3909px"><h5>QUICK LINKS</h5><ul>
  <li><span class="arrow"><svg width="7" height="7" viewBox="0 0 8 8"><path d="M2 1l3 3-3 3" stroke="#000" stroke-width="1.6" fill="none"/></svg></span>News</li>
  <li><span class="arrow"><svg width="7" height="7" viewBox="0 0 8 8"><path d="M2 1l3 3-3 3" stroke="#000" stroke-width="1.6" fill="none"/></svg></span>PrivacyPolicy</li>
  <li><span class="arrow"><svg width="7" height="7" viewBox="0 0 8 8"><path d="M2 1l3 3-3 3" stroke="#000" stroke-width="1.6" fill="none"/></svg></span>Terms Of Use</li>
</ul></div>
<div class="abs fcol" style="left:866px;top:3909px"><h5>CONTACT</h5><ul>
  <li style="height:58px;line-height:20px"><span class="ic"><svg width="11" height="14" viewBox="0 0 12 16"><path d="M6 0a6 6 0 016 6c0 4-6 10-6 10S0 10 0 6a6 6 0 016-6z" fill="#f5b301"/><circle cx="6" cy="6" r="2" fill="#0e0e0e"/></svg></span><span>421, Address line goes here<br>45452,Country Name</span></li>
  <li><span class="ic"><svg width="12" height="12" viewBox="0 0 24 24"><path d="M6.6 10.8a15 15 0 006.6 6.6l2.2-2.2c.3-.3.7-.4 1-.2 1.1.4 2.3.6 3.6.6.6 0 1 .4 1 1V20c0 .6-.4 1-1 1A17 17 0 013 4c0-.6.4-1 1-1h3.5c.6 0 1 .4 1 1 0 1.3.2 2.5.6 3.6.1.3 0 .7-.2 1z" fill="#f5b301"/></svg></span>044-555 018 274</li>
  <li><span class="ic"><svg width="13" height="10" viewBox="0 0 14 10"><rect width="14" height="10" rx="1" fill="#f5b301"/><path d="M0 1l7 5 7-5" stroke="#0e0e0e" fill="none"/></svg></span>info@dorvikelectric.example</li>
</ul></div>
<div class="abs" style="left:111px;top:4140px;width:978px;height:1px;background:#333"></div>
<div class="abs" style="left:446px;top:4156px;font-size:12px;color:var(--muted)">© 2022 <b style="color:#fff">DORVIK ELECTRIC LTD</b> &nbsp;- &nbsp;All Rights Reserved</div>
<div class="abs social" style="left:985px;top:4149px"><span style="background:#3b5a9a"></span><span style="background:#c2367a"></span><span style="background:#2aa3e0"></span></div>

</body>
</html>
```